Option Sheet

We need a one page option sheet with a left to right reading of the five options. It should be a one sheet, multiple colors and definitive separations between options This is used in a sales consultation. Backround or colors not in option need to have the follow RGB value (5 red, 20 green, 63 blue)

We added a smaller text file, please change that point

Target Market(s)

Divorce

Industry/Entity Type

Legal

Requirements
Must have
• 1) All five options left to right
• 2)language included in sheet

```html
<!DOCTYPE html>
<html lang="en">
<head>
<meta charset="utf-8">
<title>Five Options – Divorce</title>
<link rel="stylesheet" href="https://fonts.googleapis.com/css2?family=Bebas+Neue&family=Roboto+Condensed:wght@400&family=Roboto:wght@400;500&display=swap">
<style>
  :root {
    --backdrop: #d9dbe3;
    --paper: #ffffff;
    --paper-edge: #eeeff2;
    --navy: rgb(5, 20, 63);
    --navy-deep: #050f36;
    --ink: #12163a;
    --orange: #e0820f;
    --label-bg: #d7d9de;
    --text: #f2f3f7;
    --square: rgba(60, 72, 120, 0.45);
  }
  * { box-sizing: border-box; margin: 0; padding: 0; }
  html, body { width: 1150px; height: 1200px; overflow: hidden; }
  body { background: var(--backdrop); position: relative; }

  .sheet {
    position: absolute; left: 133px; top: 20px;
    width: 884px; height: 1160px;
    background: var(--paper-edge);
    display: flex; flex-direction: column;
    box-shadow: 0 10px 30px rgba(0,0,0,0.15);
  }
  .sheet-header {
    height: 161px; background: var(--paper);
    position: relative;
  }
  .sheet-title {
    position: absolute; right: 52px; top: 50px;
    font-family: "Bebas Neue", "Oswald", sans-serif;
    font-size: 84px; line-height: 0.9; color: var(--ink);
    letter-spacing: 0.5px;
  }
  .sheet-subtitle {
    position: absolute; right: 55px; top: 122px;
    font-family: "Roboto", Arial, sans-serif; font-weight: 500;
    font-size: 30px; line-height: 1; color: var(--orange);
  }

  .options { display: flex; flex-direction: column; gap: 4px; }
  .option {
    height: 193px; position: relative;
    background: linear-gradient(90deg, var(--navy-deep) 0%, var(--navy) 70%, #0b1c55 100%);
    display: flex;
  }
  .option-tab {
    width: 59px; height: 100%; background: var(--orange);
    position: relative; flex-shrink: 0;
    border-right: 4px solid var(--paper-edge);
  }
  .option-tab::after {
    content: ""; position: absolute; right: -20px; top: 50%;
    transform: translateY(-50%);
    border-top: 16px solid transparent; border-bottom: 16px solid transparent;
    border-left: 16px solid var(--orange);
  }
  .option-number {
    position: absolute; left: 0; right: 0; top: 28px; text-align: center;
    font-family: "Bebas Neue", sans-serif; font-size: 38px; line-height: 1;
    color: var(--navy-deep);
  }
  .option-word {
    position: absolute; left: 50%; top: 125px;
    transform: translate(-50%, -50%) rotate(-90deg);
    font-family: "Bebas Neue", sans-serif; font-size: 32px; line-height: 1;
    color: var(--navy-deep); letter-spacing: 1px;
  }
  .option-body { padding: 20px 0 0 53px; flex: 1; position: relative; }
  .option-heading {
    font-family: "Bebas Neue", sans-serif; font-size: 25px; line-height: 1;
    color: var(--orange); letter-spacing: 0.6px; margin-bottom: 11px;
  }
  .label {
    display: inline-block; margin-left: 35px;
    background: var(--label-bg); color: var(--navy-deep);
    font-family: "Bebas Neue", sans-serif; font-size: 14px; line-height: 1;
    padding: 1px 3px 0; letter-spacing: 0.4px;
  }
  .points { list-style: none; margin: 3px 0 8px 50px; }
  .points li {
    font-family: "Roboto Condensed", "Arial Narrow", sans-serif;
    font-size: 12.2px; line-height: 14px; color: var(--text);
    padding-left: 10px; position: relative; max-width: 480px;
  }
  .points li::before {
    content: "•"; position: absolute; left: 0; top: 0; font-size: 10px;
  }
  .decor { position: absolute; right: 0; top: 0; }
</style>
</head>
<body>
<main class="sheet">
  <header class="sheet-header">
    <h1 class="sheet-title">Five Options</h1>
    <p class="sheet-subtitle">DIVORCE</p>
  </header>

  <section class="options">
    <article class="option">
      <div class="option-tab"><span class="option-number">1</span><span class="option-word">Option</span></div>
      <div class="option-body">
        <h2 class="option-heading">Do Nothing</h2>
        <span class="label">Advantages</span>
        <ul class="points"><li>Stay married</li><li>No life Changes</li></ul>
        <span class="label">Disadvantages</span>
        <ul class="points"><li>Remain unhappy, depressed, anxious</li><li>Money and assets may disappear</li><li>What is going to change?</li></ul>
      </div>
      <svg class="decor" width="110" height="193" aria-hidden="true"><rect x="54" y="30" width="56" height="84" fill="var(--square)"/><rect x="13" y="90" width="26" height="26" fill="var(--square)"/><rect x="13" y="135" width="26" height="26" fill="var(--square)"/><rect x="54" y="135" width="26" height="26" fill="var(--square)"/></svg>
    </article>

    <article class="option">
      <div class="option-tab"><span class="option-number">2</span><span class="option-word">Option</span></div>
      <div class="option-body">
        <h2 class="option-heading">Go to Counseling</h2>
        <span class="label">Advantages</span>
        <ul class="points"><li>Reconcile marriage</li><li>Help make a better life</li></ul>
        <span class="label">Disadvantages</span>
        <ul class="points"><li>Past issues are highlighted and may drudge up old wounds</li><li>It may just clarify the reasons you need to separate and/or divorce</li><li>Both parties must be invested and willing to participate</li></ul>
      </div>
      <svg class="decor" width="110" height="193" aria-hidden="true"><rect x="54" y="30" width="56" height="84" fill="var(--square)"/><rect x="13" y="90" width="26" height="26" fill="var(--square)"/><rect x="13" y="135" width="26" height="26" fill="var(--square)"/><rect x="54" y="135" width="26" height="26" fill="var(--square)"/></svg>
    </article>

    <article class="option">
      <div class="option-tab"><span class="option-number">3</span><span class="option-word">Option</span></div>
      <div class="option-body">
        <h2 class="option-heading">Do It Yourself</h2>
        <span class="label">Advantages</span>
        <ul class="points"><li>No attorney fees</li></ul>
        <span class="label">Disadvantages</span>
        <ul class="points"><li>People often find that what is “fair,” may in fact, not be truly fair</li><li>Often times, people do not know the risks</li><li>Complicated legal system</li><li>Unsure how to complete the necessary paperwork and meet the deadlines</li></ul>
      </div>
      <svg class="decor" width="110" height="193" aria-hidden="true"><rect x="54" y="30" width="56" height="84" fill="var(--square)"/><rect x="13" y="90" width="26" height="26" fill="var(--square)"/><rect x="13" y="135" width="26" height="26" fill="var(--square)"/><rect x="54" y="135" width="26" height="26" fill="var(--square)"/></svg>
    </article>

    <article class="option">
      <div class="option-tab"><span class="option-number">4</span><span class="option-word">Option</span></div>
      <div class="option-body">
        <h2 class="option-heading">Limited Representation</h2>
        <span class="label">Advantages</span>
        <ul class="points"><li>Balance between going alone and our limited involvement in the case</li></ul>
        <span class="label">Disadvantages</span>
        <ul class="points"><li>Our terms may not benefit from our legal knowledge</li><li>The legal consequences of your legal documents will not be explained to you so that you can formulate a plan for handling the rest of your case.</li><li>Your spouse or other parties may cause your legal fees to increase significantly without action on your part</li></ul>
      </div>
      <svg class="decor" width="110" height="193" aria-hidden="true"><rect x="54" y="30" width="56" height="84" fill="var(--square)"/><rect x="13" y="90" width="26" height="26" fill="var(--square)"/><rect x="13" y="135" width="26" height="26" fill="var(--square)"/><rect x="54" y="135" width="26" height="26" fill="var(--square)"/></svg>
    </article>

    <article class="option">
      <div class="option-tab"><span class="option-number">5</span><span class="option-word">Option</span></div>
      <div class="option-body">
        <h2 class="option-heading">Hire Us</h2>
        <span class="label" style="margin-left:44px">Advantages</span>
        <ul class="points" style="margin-left:60px"><li>Gain the full benefits of our experience</li><li>Have a team of Harbor Family Law attorneys</li><li>Often saves you money in the long run</li><li>Save you time and energy</li></ul>
        <span class="label" style="margin-left:44px">Disadvantages</span>
        <ul class="points" style="margin-left:60px"><li>Initial Cost</li></ul>
      </div>
      <svg class="decor" width="110" height="193" aria-hidden="true"><rect x="54" y="30" width="56" height="84" fill="var(--square)"/><rect x="13" y="90" width="26" height="26" fill="var(--square)"/><rect x="13" y="135" width="26" height="26" fill="var(--square)"/><rect x="54" y="135" width="26" height="26" fill="var(--square)"/></svg>
    </article>
  </section>
</main>
</body>
</html>
```